Veldmark Supplies Business Card

Professional business card that stand out to our potential customers. Front and back with clean modern design

Industry/Entity Type

Oil and gas

Contact Information for Business Card

Name, address, website , office phone and cell number

Requirements
Must have
• Editable files for each employee

```html
<!DOCTYPE html>
<html lang="en">
<head>
<meta charset="utf-8">
<title>Veldmark Supplies Business Card</title>
<link rel="stylesheet" href="https://fonts.googleapis.com/css2?family=Montserrat:wght@400;500;800&display=swap">
<style>
  :root {
    --backdrop: #d9dadc;
    --card-white: #ffffff;
    --brand-red: #ec1f27;
    --brand-cyan: #0bb0d3;
    --ink: #1c1c1c;
  }
  * { margin: 0; padding: 0; box-sizing: border-box; }
  html, body {
    width: 1200px; height: 856px; overflow: hidden;
    background: var(--backdrop);
    font-family: "Montserrat", sans-serif;
  }
  .canvas {
    width: 1200px; height: 856px;
    display: flex; align-items: center; justify-content: center; gap: 40px;
  }
  .card {
    position: relative; width: 540px; height: 309px; overflow: hidden;
    box-shadow: 0 10px 26px rgba(0,0,0,.22);
  }
  .card-front { background: var(--card-white); }
  .card-back { background: var(--brand-cyan); display: flex; align-items: center; justify-content: center; }
  .swoosh { position: absolute; inset: 0; width: 100%; height: 100%; }

  .wordmark {
    display: flex; align-items: center; gap: 10px;
    font-weight: 800; text-transform: uppercase; letter-spacing: .5px;
  }
  .wordmark-square { display: block; flex: none; }
  .front-wordmark {
    position: absolute; left: 34px; top: 118px;
    color: var(--brand-red); font-size: 19px; line-height: 1.15;
    align-items: flex-start;
  }
  .front-wordmark .wordmark-square { width: 16px; height: 16px; background: var(--brand-red); margin-top: 3px; }
  .back-wordmark { color: var(--card-white); font-size: 36px; }
  .back-wordmark .wordmark-square { width: 32px; height: 32px; background: var(--card-white); }

  .accent-lines { position: absolute; left: 180px; top: 92px; width: 60px; height: 130px; }

  .contact { position: absolute; left: 262px; top: 28px; color: var(--ink); }
  .contact-name { color: var(--brand-red); font-weight: 800; font-size: 21px; letter-spacing: .5px; text-transform: uppercase; }
  .contact-title { font-size: 12px; font-weight: 500; margin-top: 2px; }
  .contact-address { font-size: 12px; line-height: 1.35; margin-top: 10px; }
  .contact-list { list-style: none; margin-top: 8px; font-size: 12px; }
  .contact-list li { display: flex; align-items: center; gap: 8px; height: 19px; }
  .contact-icon { width: 14px; height: 14px; flex: none; }
  .highlight { color: var(--brand-red); }
</style>
</head>
<body>
<main class="canvas">
  <section class="card card-front" aria-label="Card front">
    <svg class="swoosh" viewBox="0 0 540 309" preserveAspectRatio="none" aria-hidden="true">
      <path d="M92,309 C250,258 420,228 540,206 L540,309 Z" fill="var(--brand-red)"/>
      <path d="M118,309 C268,266 430,240 540,222 L540,309 Z" fill="var(--card-white)"/>
      <path d="M126,309 C274,270 434,245 540,228 L540,309 Z" fill="var(--brand-cyan)"/>
    </svg>

    <div class="wordmark front-wordmark">
      <span class="wordmark-square"></span>
      <span>Veldmark<br>Supplies</span>
    </div>

    <svg class="accent-lines" viewBox="0 0 60 130" aria-hidden="true">
      <line x1="6" y1="4" x2="56" y2="126" stroke="var(--brand-cyan)" stroke-width="1"/>
      <line x1="20" y1="10" x2="54" y2="96" stroke="var(--brand-red)" stroke-width="1"/>
      <line x1="10" y1="26" x2="44" y2="112" stroke="var(--brand-red)" stroke-width="1"/>
    </svg>

    <div class="contact">
      <p class="contact-name">Dorin Halvers</p>
      <p class="contact-title">President</p>
      <p class="contact-address">482 Larkspur Ave, Ste<br>210, Corvane, TX 75390</p>
      <ul class="contact-list">
        <li>
          <svg class="contact-icon" viewBox="0 0 14 14" aria-hidden="true"><rect width="14" height="14" fill="var(--brand-red)"/><path d="M4 3.5h2l.6 2-1 .8a5 5 0 0 0 2.1 2.1l.8-1 2 .6v2c-3.8.3-6.8-2.7-6.5-6.5z" fill="#fff"/></svg>
          <span>555-214-3870</span>
        </li>
        <li>
          <svg class="contact-icon" viewBox="0 0 14 14" aria-hidden="true"><rect width="14" height="14" fill="var(--brand-red)"/><rect x="4.5" y="2.5" width="5" height="9" rx="1" fill="none" stroke="#fff"/><circle cx="7" cy="10" r=".6" fill="#fff"/></svg>
          <span>555-000-0199</span>
        </li>
        <li>
          <svg class="contact-icon" viewBox="0 0 14 14" aria-hidden="true"><rect width="14" height="14" fill="var(--brand-red)"/><rect x="2.5" y="4" width="9" height="6" fill="none" stroke="#fff"/><path d="M2.5 4l4.5 3.5L11.5 4" fill="none" stroke="#fff"/></svg>
          <span>info@example-youremail.com</span>
        </li>
        <li>
          <svg class="contact-icon" viewBox="0 0 14 14" aria-hidden="true"><rect width="14" height="14" fill="var(--brand-red)"/><circle cx="7" cy="7" r="4" fill="none" stroke="#fff"/><path d="M3 7h8M7 3c-2 2.5-2 5.5 0 8M7 3c2 2.5 2 5.5 0 8" fill="none" stroke="#fff" stroke-width=".8"/></svg>
          <span>www.<span class="highlight">example-yourwebsite</span>.com</span>
        </li>
      </ul>
    </div>
  </section>

  <section class="card card-back" aria-label="Card back">
    <div class="wordmark back-wordmark">
      <span class="wordmark-square"></span>
      <span>Veldmark Supplies</span>
    </div>
  </section>
</main>
</body>
</html>
```